Investment firm needs website redesign

we want to change our site with a trendy new design. We are an investment trading firm dealing in currencies etc for retail clients. We are looking for new ideas for our website design which shows class and international reach. We want the inner pages also to be designed especially the look. We do not want the typical designs used by most sites and are looking for something new and interesting. you can review our current site www.trovanique-exchange.com.

Target Market(s)

international

Industry/Entity Type

Forex

Coding

Coded - Design and coding required

Number of Pages Required

5+ page

Font styles to use
Sans Serif

Colors

Designer to choose colors to be used in the design.

Requirements
Must have
• responsive, easy to load
Nice to have
• something trendy yet sophisticated. technology is an important part of our business
Should not have
• do not want the typical designs used by most websites

```html
<!DOCTYPE html>
<html lang="en">
<head>
<meta charset="utf-8">
<title>Veranth Markets</title>
<link href="https://fonts.googleapis.com/css2?family=Raleway:wght@600;700;800&family=Open+Sans:wght@400;600;700&display=swap" rel="stylesheet">
<style>
:root{
  --navy:#15212c;
  --navy-2:#1d2b38;
  --yellow:#f2b731;
  --yellow-dark:#d99f1c;
  --ink:#1b1f24;
  --text:#3a3f45;
  --muted:#8a9099;
  --light:#eef0f3;
  --white:#ffffff;
}
*{margin:0;padding:0;box-sizing:border-box}
html,body{width:1200px;height:3543px;overflow:hidden;background:var(--white)}
body{font-family:"Open Sans",Arial,sans-serif;color:var(--text);position:relative}
.abs{position:absolute}
a{color:inherit;text-decoration:none}

/* ticker */
.ticker{top:0;left:0;width:1200px;height:36px;background:var(--yellow)}
.ticker-label{top:0;left:0;width:283px;height:36px;background:var(--navy);color:var(--white);font:700 15px "Raleway",sans-serif;line-height:36px;padding-left:162px;letter-spacing:.5px}
.ticker-items{left:305px;top:0;line-height:36px;font-size:11px;font-weight:600;color:var(--navy);display:flex;gap:40px}
.ticker-items .up{color:#1a5b2a}.ticker-items .down{color:#9b1d12}

/* header */
.logo{top:80px;left:160px;display:flex;align-items:center;gap:12px;font:800 28px "Raleway",sans-serif;color:var(--navy);letter-spacing:.5px}
.logo-mark{width:38px;height:38px;border-radius:50%;background:var(--navy)}
.top-nav{top:66px;left:443px;display:flex;gap:22px;font:700 11px "Raleway",sans-serif;color:var(--navy);text-transform:uppercase}
.main-nav{top:113px;left:400px;width:800px;height:47px;background:var(--navy);display:flex;align-items:center;gap:27px;padding-left:42px;font:700 12px "Raleway",sans-serif;color:var(--white);text-transform:uppercase}

/* hero */
.hero{top:160px;left:0;width:1200px;height:525px;background:linear-gradient(120deg,#c9ccd0 0%,#e9eaec 35%,#8d8f93 60%,#2a2d31 100%)}
.hero-dots{top:630px;left:510px;display:flex;gap:6px}
.hero-dots span{width:34px;height:5px;background:var(--navy)}
.hero-dots span.on{background:#555}

/* sections */
h2{font:800 23px "Raleway",sans-serif;color:var(--ink);text-transform:uppercase;letter-spacing:.5px}
.para{font-size:11.5px;line-height:21px;color:var(--text)}
.btn{display:block;width:108px;height:38px;border-radius:19px;background:var(--yellow);color:var(--white);font:700 10px "Raleway",sans-serif;text-transform:uppercase;text-align:center;line-height:38px}

.steps-title{top:752px;left:0;width:1200px;text-align:center}
.steps-text{top:796px;left:300px;width:600px;text-align:center;font-size:11px;line-height:18px}
.step{top:880px;width:180px;text-align:center;font:700 14px "Open Sans",sans-serif;color:var(--ink)}
.step-icon{width:96px;height:96px;border-radius:50%;border:3px solid var(--yellow);margin:0 auto 14px;display:flex;align-items:center;justify-content:center;background:var(--white)}
.steps-btn{top:1063px;left:535px;width:124px}

.band{left:0;width:1200px}
.band-multi{top:1157px;height:485px;background:linear-gradient(90deg,#eceef1,#f7f8f9 60%,#e6e9ed)}
.band-contract{top:1642px;height:491px;background:linear-gradient(90deg,#e8ebee,#f6f7f8 55%,#eef0f2)}
.band-account{top:2133px;height:484px;background:linear-gradient(90deg,#f7f8f9,#eef0f2 60%,#e5e8ec)}

.feature-title{width:420px}
.feature-text{width:400px}
.art{border-radius:6px}

.demo-title{top:2700px;left:0;width:1200px;text-align:center}
.demo-text{top:2742px;left:340px;width:520px;text-align:center;font-size:11px;line-height:19px}
.demo-btn{top:2834px;left:532px;width:136px}
.rule{top:2952px;left:163px;width:874px;height:1px;background:#dfe2e6}

.badges{top:3028px;left:323px;display:flex;gap:42px;align-items:center}
.badge{height:46px;border-radius:6px;background:#d9dde2}
.badge.dark{background:var(--navy)}
.badge.round{border-radius:50%;width:46px}

.news-band{top:3108px;left:0;width:1200px;height:100px;background:var(--yellow)}
.news{top:3141px;left:163px;width:874px;height:36px;background:var(--white);display:flex;align-items:center;font-size:12px}
.news-label{background:var(--navy);color:var(--white);font:700 14px "Raleway",sans-serif;height:36px;line-height:36px;padding:0 20px 0 12px;text-transform:uppercase}
.news-date{font:700 10px "Open Sans",sans-serif;color:var(--navy);padding:0 14px;border-right:1px solid #ccc;text-transform:uppercase}
.news-text{padding-left:14px;color:var(--ink)}

.footer{top:3208px;left:0;width:1200px;height:335px;background:var(--navy)}
.foot-col{top:3256px;color:var(--white)}
.foot-col h4{font:700 12px "Raleway",sans-serif;text-transform:uppercase;margin-bottom:14px;letter-spacing:.3px}
.foot-col li{list-style:none;font-size:11px;line-height:19.6px;color:#d8dde2}
.social{top:3437px;left:500px;display:flex;gap:16px}
.social span{width:17px;height:17px;border-radius:50%;background:var(--white)}
.foot-rule{top:3489px;left:163px;width:874px;height:1px;background:#34414e}
.copyright{top:3510px;left:0;width:1200px;text-align:center;font-size:10.5px;color:#c9cfd5}
</style>
</head>
<body>

<div class="abs ticker"></div>
<div class="abs ticker-label">LIVE MARKET</div>
<div class="abs ticker-items">
  <span>INDEX 50 &nbsp;8,936 <span class="up">▲ 55.55 (+0.6%)</span></span>
  <span>DOLLAR RUPEE &nbsp;66.84 <span class="up">▲ 0.15 (+0.2%)</span></span>
  <span>GOLD &nbsp;29,351 <span class="down">▼ 171.00 (-0.58%)</span></span>
</div>

<div class="abs logo"><span class="logo-mark"></span>VERANTH MARKETS</div>
<nav class="abs top-nav">
  <a>About Veranth</a><a>Products &amp; Services</a><a>Open Account</a><a>Trading Platform</a><a>Trading Info</a><a>Research</a>
</nav>
<nav class="abs main-nav">
  <a>CFDs</a><a>Spot</a><a>Futures</a><a>Options</a><a>Bonds</a><a>Stocks</a><a>Web Login</a><a>Mobile Trading</a>
</nav>

<div class="abs hero" role="img" aria-label="Photo of hands using a tablet with financial charts on an office desk"></div>
<div class="abs hero-dots"><span></span><span class="on"></span><span></span><span></span></div>

<h2 class="abs steps-title">3 Easy Steps to Start Trading</h2>
<p class="abs steps-text">Sed ut perspiciatis unde omnis iste natus error sit voluptatem accusantium doloremque laudantium, totam rem aperiam, eaque ipsa quae ab illo inventore veritatis et quasi architecto beate</p>

<div class="abs step" style="left:288px">
  <div class="step-icon"><svg width="44" height="44" viewBox="0 0 44 44" fill="none" stroke="#1b1f24" stroke-width="2"><rect x="8" y="5" width="24" height="32" rx="2"/><path d="M13 13h14M13 19h14M13 25h9"/><path d="M30 22l8-8 3 3-8 8-4 1z"/></svg></div>
  Complete the<br>online Application
</div>
<div class="abs step" style="left:503px">
  <div class="step-icon"><svg width="44" height="44" viewBox="0 0 44 44" fill="none" stroke="#1b1f24" stroke-width="2"><circle cx="15" cy="14" r="6"/><circle cx="29" cy="14" r="6"/><path d="M4 36c0-7 5-12 11-12s11 5 11 12M18 36c0-7 5-12 11-12s11 5 11 12"/></svg></div>
  Find Your Account
</div>
<div class="abs step" style="left:725px">
  <div class="step-icon"><svg width="44" height="44" viewBox="0 0 44 44" fill="#1b1f24"><rect x="6" y="28" width="6" height="10"/><rect x="15" y="22" width="6" height="16"/><rect x="24" y="17" width="6" height="21"/><rect x="33" y="11" width="6" height="27"/><path d="M5 22L18 11l6 5 12-11" fill="none" stroke="#1b1f24" stroke-width="2.5"/></svg></div>
  Start Trading
</div>
<a class="abs btn steps-btn">Read More</a>

<section class="abs band band-multi"></section>
<h2 class="abs feature-title" style="top:1304px;left:163px">Multi-Account Manager</h2>
<p class="abs para feature-text" style="top:1352px;left:163px">Lorem ipsum dolor sit amet, consectetur adipiscing elit, sed do eiusmod tempor incididunt ut labore et dolore magna aliqua. Ut enim ad minim veniam, quis nost rud exercitation ullamco laboris nisi ut aliquip ex ea commodo consequat.uis au te irure dolor in reprehenderit in voluptate velit esse cillum dolore eu fugiat null a pariaturcepteur sint occaecat cupid.</p>
<a class="abs btn" style="top:1483px;left:163px">Read More</a>
<div class="abs art" style="top:1268px;left:619px;width:420px;height:267px;background:linear-gradient(135deg,#1c2530,#0f3550 55%,#d8dde2)" role="img" aria-label="Illustration of a laptop and monitor showing trading charts"></div>

<section class="abs band band-contract"></section>
<div class="abs art" style="top:1748px;left:236px;width:267px;height:331px;background:linear-gradient(160deg,#ffffff,#efe6d4 60%,#e6a93a)" role="img" aria-label="Illustration of contract papers with a pen and seal"></div>
<h2 class="abs feature-title" style="top:1798px;left:642px">Contract Specifications</h2>
<p class="abs para feature-text" style="top:1846px;left:642px">Lorem ipsum dolor sit amet, consectetur adipiscing elit, sed do eiusmod tempor incididunt ut labore et dolore magna aliqua. Ut enim ad minim veniam, quis nost rud exercitation ullamco laboris nisi ut aliquip ex ea commodo consequat.uis au te irure dolor in reprehenderit in voluptate velit esse cillum dolore eu fugiat null a pariaturcepteur sint occaecat cupid.</p>
<a class="abs btn" style="top:1977px;left:642px">Read More</a>

<section class="abs band band-account"></section>
<h2 class="abs feature-title" style="top:2284px;left:163px">How to Open an Account</h2>
<p class="abs para feature-text" style="top:2332px;left:163px">Lorem ipsum dolor sit amet, consectetur adipiscing elit, sed do eiusmod tempor incididunt ut labore et dolore magna aliqua. Ut enim ad minim veniam, quis nost rud exercitation ullamco laboris nisi ut aliquip ex ea commodo consequat.uis au te irure dolor in reprehenderit in voluptate velit esse cillum dolore eu fugiat null a pariaturcepteur sint occaecat cupid.</p>
<a class="abs btn" style="top:2466px;left:163px">Read More</a>
<div class="abs art" style="top:2165px;left:661px;width:390px;height:305px;background:linear-gradient(135deg,#f0c45a,#c99524 45%,#1e2630 75%)" role="img" aria-label="Illustration of gold coins beside a phone showing a crypto chart"></div>

<h2 class="abs demo-title">Create a Demo Account Now</h2>
<p class="abs demo-text">Lorem ipsum dolor sit amet, consectetur adipiscing elit, sed do eiusmod tempor incididunt ut labore e magna aliqua. Ut enim ad minim veniam, quis nostrud exercitation ullamco laboris nisi ut aliquip ex ea codo consequat.uis aute irure dolor in reprehenderit in voluptate velit esse cillum dolore eu fug.</p>
<a class="abs btn demo-btn">Try It for Free</a>
<div class="abs rule"></div>

<div class="abs badges">
  <span class="badge round"></span>
  <span class="badge" style="width:96px"></span>
  <span class="badge" style="width:112px"></span>
  <span class="badge round"></span>
  <span class="badge dark" style="width:128px"></span>
</div>

<div class="abs news-band"></div>
<div class="abs news">
  <span class="news-label">Latest News</span>
  <span class="news-date">June 05 2018</span>
  <span class="news-text">Sed ut perspiciatis unde omnis iste natus error sit voluptatem accusantium.</span>
  <svg style="margin-left:auto;margin-right:10px" width="18" height="12" viewBox="0 0 18 12" fill="none" stroke="#888" stroke-width="1.5"><path d="M6 1L1 6l5 5M12 1l5 5-5 5"/></svg>
</div>

<footer class="abs footer"></footer>
<div class="abs foot-col" style="left:163px"><h4>Company</h4><ul><li>Our Regulator</li><li>Compliance</li><li>Auditor</li><li>Global Network</li></ul></div>
<div class="abs foot-col" style="left:342px"><h4>Products</h4><ul><li>CFDs</li><li>Forex</li><li>Futures</li><li>Stocks</li><li>Bonds</li><li>Options</li></ul></div>
<div class="abs foot-col" style="left:500px"><h4>Trading Platforms</h4><ul><li>Orion Pro</li><li>Orion Trader</li><li>Demo</li><li>System Manual</li></ul></div>
<div class="abs foot-col" style="left:709px"><h4>Partner Program</h4><ul><li>Ibs</li><li>White Labels</li><li>Open An Account</li><li>Account Form</li><li>Product Guide</li></ul></div>
<div class="abs foot-col" style="left:914px"><h4>Trading Info</h4><ul><li>Product Guide</li><li>Contract Specifications</li><li>Margins and Spreads</li><li>Contract Calendar</li><li>Code Of Conduct</li><li>Execution Terms</li><li>Order Types</li><li>Online Trading</li></ul></div>
<div class="abs social"><span></span><span></span><span></span><span></span><span></span><span></span></div>
<div class="abs foot-rule"></div>
<p class="abs copyright">Copyright © 2018 www.trovanique-exchange.com. All rights reserved.</p>

</body>
</html>
```